Presentation and Communication Coaching Services Business needs updated interactive web site

I want to keep the color scheme, functionality, and pages of my current site, but with a newer/updated look. I need to improve security and simplify images, etc. (Please see current site http://brightwellvoicetutor.com ) This will need be functional on mobile devices, as well.

I'm attached to the scrolling client list and scrolling client feedback.

Industry/Entity Type

Professional Service

Font styles to use
Sans Serif

Colors
0356a4
f37122
33a6d7

Requirements
Must have
• scrolling client banner on home page, client comments slider, color scheme
• Please see current site: http://brightwellvoicetutor.com
Nice to have
• better action/appearance
Should not have
• I don't want it to look like all the other sites/templates

```html
<!DOCTYPE html>
<html lang="en">
<head>
<meta charset="utf-8">
<title>Brightwell Voice Tutoring</title>
<link href="https://fonts.googleapis.com/css2?family=Questrial&display=swap" rel="stylesheet">
<style>
:root{
  --ink:#0f3446;
  --ink-deep:#0b2a39;
  --band:#14445a;
  --gold:#e8ac2c;
  --gold-soft:#f1bf45;
  --sky:#33a6d7;
  --white:#ffffff;
  --mist:#c7d6de;
  --muted:#8fa8b5;
}
*{box-sizing:border-box;margin:0;padding:0}
html,body{width:1200px;height:3502px;overflow:hidden}
body{background:var(--ink);color:var(--white);font-family:"Questrial",Arial,sans-serif;position:relative}
.abs{position:absolute}

/* header */
.site-header{left:0;top:0;width:1200px;height:120px;z-index:3}
.brand{left:72px;top:40px;font-size:30px;color:var(--gold);letter-spacing:-.3px}
.nav{left:420px;top:49px;display:flex;gap:27px;font-size:12.5px}
.nav a{color:var(--white);text-decoration:none}
.nav a.active{color:var(--gold)}
.login{left:990px;top:38px;width:134px;height:34px;border-radius:17px;background:var(--sky);font-size:12.5px;display:flex;align-items:center;justify-content:center;gap:8px}

/* hero */
.hero{left:0;top:0;width:1200px;height:400px;
  background:
    radial-gradient(circle at 444px 160px,rgba(95,190,200,.55) 0,rgba(60,150,165,.35) 70px,rgba(30,90,110,0) 140px),
    radial-gradient(ellipse 120px 260px at 444px 330px,rgba(10,30,40,.55) 0,rgba(10,30,40,0) 100%),
    radial-gradient(ellipse 380px 220px at 760px 60px,rgba(150,175,185,.28) 0,rgba(150,175,185,0) 100%),
    radial-gradient(ellipse 300px 200px at 1000px 230px,rgba(120,150,165,.18) 0,rgba(120,150,165,0) 100%),
    linear-gradient(180deg,#1c4a5e 0%,#153e51 60%,#0f3446 100%)}
.hero-quote{left:300px;top:202px;width:600px;text-align:center;font-style:italic;font-size:21px;line-height:29px;color:var(--white)}
.dots{left:563px;top:372px;display:flex;gap:6px}
.dots span{width:9px;height:9px;border-radius:50%;border:1px solid var(--muted)}
.dots span.on{background:var(--muted)}

/* intro */
.intro-photo{left:150px;top:450px;width:450px;height:300px;
  background:
    radial-gradient(ellipse 90px 80px at 150px 95px,rgba(235,215,170,.9) 0,rgba(235,215,170,0) 100%),
    radial-gradient(ellipse 140px 110px at 150px 220px,rgba(225,235,245,.95) 0,rgba(225,235,245,0) 100%),
    radial-gradient(ellipse 90px 140px at 395px 130px,rgba(210,185,165,.85) 0,rgba(210,185,165,0) 100%),
    radial-gradient(ellipse 120px 90px at 330px 270px,rgba(140,100,70,.8) 0,rgba(140,100,70,0) 100%),
    linear-gradient(120deg,#eef0ea 0%,#c9cdbf 40%,#8d9a86 70%,#5f6a62 100%)}
.intro-title{left:638px;top:470px;font-size:29px;line-height:34px;color:var(--gold);font-weight:400}
.intro-text{left:638px;top:552px;width:410px;font-size:12.5px;line-height:19.5px;color:var(--mist)}
.intro-text p+p{margin-top:14px}

/* clients */
.clients{left:0;top:824px;width:1200px;height:112px;background:var(--band);display:flex;align-items:center;justify-content:space-around;padding:0 60px}
.client{font-size:18px;color:#5fb3d6}
.client.strong{color:var(--white)}

/* process */
.process{left:0;top:936px;width:1200px;height:450px;background:linear-gradient(90deg,#163f52 0%,#1b475b 55%,#2a5568 100%)}
.process-photo{left:640px;top:936px;width:560px;height:450px;
  background:
    radial-gradient(ellipse 90px 110px at 270px 90px,rgba(225,200,150,.75) 0,rgba(225,200,150,0) 100%),
    radial-gradient(ellipse 80px 90px at 300px 170px,rgba(215,180,160,.7) 0,rgba(215,180,160,0) 100%),
    radial-gradient(ellipse 150px 180px at 300px 360px,rgba(20,30,40,.75) 0,rgba(20,30,40,0) 100%),
    radial-gradient(ellipse 120px 200px at 480px 150px,rgba(110,130,135,.45) 0,rgba(110,130,135,0) 100%),
    linear-gradient(90deg,rgba(27,71,91,0) 0%,rgba(70,95,105,.5) 40%,rgba(50,70,80,.6) 100%)}
.step{width:200px;text-align:center}
.step .disc{width:112px;height:112px;margin:0 auto;border-radius:50%;background:var(--gold);display:flex;align-items:center;justify-content:center}
.step .disc.light{background:var(--white)}
.step h3{margin-top:26px;font-size:17px;font-weight:400}
.step h3.gold{color:var(--gold)}
.step p{margin-top:12px;font-size:12px;line-height:18px;color:var(--mist)}
.spark{stroke:var(--muted);stroke-width:1.2}

/* services */
.section-title{left:0;width:1200px;text-align:center;font-size:28px;color:var(--gold);font-weight:400}
.tile{overflow:hidden}
.tile .fill{position:absolute;inset:0}
.tile h4{position:absolute;left:74px;font-size:18px;font-weight:400;color:var(--gold)}
.tile p{position:absolute;left:74px;font-size:12.5px;line-height:19px;color:var(--white)}
.more{position:absolute;left:74px;width:74px;height:30px;border-radius:15px;background:var(--sky);font-size:12px;display:flex;align-items:center;justify-content:center}

/* publications */
.cover{width:210px;height:268px}
.caption{width:210px;text-align:center;font-size:13px;line-height:18px}

/* training */
.training{left:0;top:2522px;width:1200px;height:525px;background:var(--band)}
.sub{left:0;width:1200px;text-align:center;font-size:14px;color:var(--mist)}
.sub em{font-style:normal;color:var(--gold)}
.checklist{left:150px;top:2690px;width:400px;list-style:none}
.checklist li{display:flex;gap:12px;font-size:12.5px;line-height:18px;margin-bottom:4.5px;color:var(--mist)}
.checklist svg{flex:none;margin-top:2px}
.video{left:602px;top:2673px;width:447px;height:299px;
  background:
    radial-gradient(ellipse 100px 130px at 225px 150px,rgba(235,190,160,.85) 0,rgba(235,190,160,0) 100%),
    radial-gradient(ellipse 150px 170px at 225px 170px,rgba(60,35,25,.7) 0,rgba(60,35,25,0) 100%),
    radial-gradient(ellipse 200px 120px at 225px 310px,rgba(110,110,120,.8) 0,rgba(110,110,120,0) 100%),
    linear-gradient(90deg,#e39a3d 0%,#d7893a 30%,#c07a3a 70%,#e3a048 100%)}
.play{left:800px;top:2798px}

/* signup */
.signup{left:0;top:3047px;width:1200px;height:117px;background:var(--gold)}
.signup-text{left:150px;top:3084px;width:420px;font-size:17px;line-height:21px;color:var(--ink)}
.field{left:600px;top:3087px;width:450px;height:46px;border-radius:23px;border:1.5px solid var(--ink);background:var(--gold-soft)}
.field span{position:absolute;left:24px;top:14px;font-size:13px;color:var(--ink)}
.register{left:870px;top:3087px;width:180px;height:46px;border-radius:23px;background:var(--ink);font-size:13px;display:flex;align-items:center;justify-content:center}

/* footer */
.footer{left:0;top:3164px;width:1200px;height:292px;background:var(--ink-deep)}
.f-name{left:150px;top:3228px;font-size:25px;color:var(--gold)}
.f-role{left:150px;top:3264px;font-size:12px;color:var(--mist)}
.f-text{left:150px;top:3294px;width:380px;font-size:12px;line-height:19px;color:var(--muted)}
.consult{left:150px;top:3390px;width:112px;height:30px;border-radius:15px;border:1px solid var(--sky);color:var(--sky);font-size:11px;display:flex;align-items:center;justify-content:center}
.f-call{left:638px;top:3228px;font-size:27px;color:var(--sky)}
.f-mail{left:640px;top:3264px;font-size:13px;color:var(--white)}
.social{left:638px;top:3296px;display:flex;gap:10px}
.social span{width:26px;height:26px;border-radius:50%;border:1px solid var(--sky)}
.social span.on{background:var(--sky)}
.f-links{left:638px;top:3395px;font-size:11px;color:var(--mist)}
.totop{left:1112px;top:3236px}
.copyright{left:0;top:3456px;width:1200px;height:46px;background:#0a2533;font-size:11px;color:var(--muted);padding:15px 150px}
</style>
</head>
<body>

<!-- hero -->
<div class="abs hero" role="img" aria-label="Dim stage backdrop with a lit microphone and drifting haze"></div>
<header class="abs site-header">
  <div class="abs brand">brightwellvoicetutor</div>
  <nav class="abs nav">
    <a class="active" href="#">Home</a><a href="#">About</a><a href="#">Clients</a><a href="#">Reviews</a><a href="#">Services</a><a href="#">Contact</a><a href="#">Speaking Secrets</a>
  </nav>
  <div class="abs login">
    <svg width="14" height="14" viewBox="0 0 14 14"><circle cx="7" cy="7" r="6" fill="none" stroke="#fff" stroke-width="1.2"/><circle cx="7" cy="5.5" r="2" fill="#fff"/><path d="M3.5 11a3.5 3 0 0 1 7 0" fill="#fff"/></svg>
    Client Login
  </div>
</header>
<blockquote class="abs hero-quote">I was the first to present and they were really interested in some of the key stuff, they were throwing questions left/right. Ended up being up on the stage for 1 hour and 10 min! It was really great!</blockquote>
<div class="abs dots"><span class="on"></span><span></span><span></span><span></span><span></span></div>

<!-- intro -->
<div class="abs intro-photo" role="img" aria-label="Coach gesturing while speaking to a colleague at a meeting table"></div>
<h2 class="abs intro-title">You're good at what you do.<br>Learn How to let it show.</h2>
<div class="abs intro-text">
  <p>An individual works hard to reach a place of respect and authority in her or his chosen profession. Effective self-presentation adds confidence and allows one's unique personality and expertise to shine through – in fact, it is key in separating from the pack and reaching higher goals. As competition increases, these skills become more essential in demonstrating value to an employer, manager, or board.</p>
  <p>You've done your best to reach this professional level. It's time to develop what it takes to reach the next one.</p>
</div>

<!-- clients -->
<div class="abs clients">
  <span class="client">Wexmoor</span>
  <span class="client strong">ClearPoint</span>
  <span class="client">Larkhaven</span>
  <span class="client">Tidewell</span>
  <span class="client">Nuvaro Health</span>
  <span class="client" style="font-size:14px;line-height:16px;text-align:center">Harlow + Penn<br>Interiors</span>
</div>

<!-- process -->
<div class="abs process"></div>
<div class="abs process-photo" role="img" aria-label="Woman speaking into a microphone at a podium"></div>
<svg class="abs" style="left:0;top:936px" width="1200" height="450">
  <g class="spark">
    <line x1="192" y1="92" x2="216" y2="116"/><line x1="336" y1="92" x2="312" y2="116"/>
    <line x1="416" y1="92" x2="440" y2="116"/><line x1="560" y1="92" x2="536" y2="116"/>
    <line x1="640" y1="92" x2="664" y2="116"/><line x1="784" y1="92" x2="760" y2="116"/>
    <line x1="866" y1="92" x2="890" y2="116"/><line x1="1010" y1="92" x2="986" y2="116"/>
  </g>
</svg>
<div class="abs step" style="left:164px;top:1034px">
  <div class="disc"><svg width="44" height="44" viewBox="0 0 44 44" fill="none" stroke="#fff" stroke-width="3"><path d="M12 6h20v10a10 10 0 0 1-20 0z"/><path d="M12 10H5a7 7 0 0 0 7 9M32 10h7a7 7 0 0 1-7 9"/><path d="M22 26v8M14 38h16"/></svg></div>
  <h3>The Goal</h3>
</div>
<div class="abs step" style="left:388px;top:1034px">
  <div class="disc light"><svg width="48" height="44" viewBox="0 0 48 44" fill="none" stroke="#e8ac2c" stroke-width="3"><circle cx="18" cy="24" r="9"/><circle cx="18" cy="24" r="3"/><circle cx="34" cy="12" r="6"/><circle cx="34" cy="12" r="2"/></svg></div>
  <h3 class="gold">The Challenge</h3>
  <p>Find a path to develop skills and strategies to accomplish this aim while also projecting confidence, warmth, and credibility.</p>
</div>
<div class="abs step" style="left:612px;top:1034px">
  <div class="disc"><svg width="44" height="44" viewBox="0 0 44 44" fill="none" stroke="#fff" stroke-width="3"><path d="M8 14h9a5 5 0 1 1 10 0h9v9a5 5 0 1 0 0 10v5H8v-9a5 5 0 1 0 0-10z"/></svg></div>
  <h3>The Solution</h3>
</div>
<div class="abs step" style="left:838px;top:1034px">
  <div class="disc"><svg width="44" height="44" viewBox="0 0 44 44" fill="none" stroke="#fff" stroke-width="3"><path d="M6 8v30h32"/><path d="M10 32l8-10 7 5 11-13"/></svg></div>
  <h3>The Result</h3>
</div>

<!-- services -->
<h2 class="abs section-title" style="top:1424px">Services We Provide</h2>
<div class="abs tile" style="left:0;top:1501px;width:712px;height:260px">
  <div class="fill" role="img" aria-label="Coach leading a one-on-one session" style="background:
    radial-gradient(ellipse 70px 90px at 320px 60px,rgba(230,215,190,.7) 0,rgba(230,215,190,0) 100%),
    radial-gradient(ellipse 120px 110px at 330px 160px,rgba(220,230,235,.6) 0,rgba(220,230,235,0) 100%),
    radial-gradient(ellipse 110px 90px at 560px 220px,rgba(40,60,70,.6) 0,rgba(40,60,70,0) 100%),
    linear-gradient(90deg,#2b5566 0%,#6f8c97 45%,#a9bcc2 65%,#4b6e7c 100%)"></div>
  <h4 style="top:152px">Coaching</h4>
  <p style="top:180px;width:560px">One-on-one, individual and customized to your unique goals, obstacles, and challenges. In person, or via video conference.</p>
</div>
<div class="abs tile" style="left:716px;top:1501px;width:484px;height:260px">
  <div class="fill" role="img" aria-label="Executives talking around a conference table" style="background:
    radial-gradient(ellipse 70px 80px at 420px 60px,rgba(210,175,150,.75) 0,rgba(210,175,150,0) 100%),
    radial-gradient(ellipse 60px 70px at 220px 100px,rgba(215,190,170,.6) 0,rgba(215,190,170,0) 100%),
    radial-gradient(ellipse 120px 80px at 430px 220px,rgba(30,40,60,.7) 0,rgba(30,40,60,0) 100%),
    linear-gradient(90deg,#4a7182 0%,#9fb4bb 50%,#c8d3d6 75%,#6b8793 100%)"></div>
  <h4 style="left:70px;top:152px">Accents</h4>
  <p style="left:70px;top:180px;width:390px">Support for executives from outside the U.S. to increase intelligibility and diminish obstacles to successful communication in American English.</p>
</div>
<div class="abs tile" style="left:0;top:1765px;width:484px;height:257px">
  <div class="fill" role="img" aria-label="Workshop participants in a bright room" style="background:
    radial-gradient(ellipse 110px 90px at 300px 60px,rgba(140,170,180,.45) 0,rgba(140,170,180,0) 100%),
    linear-gradient(90deg,#1d4c60 0%,#2f6176 55%,#3f6f82 80%,#2a5a6e 100%)"></div>
  <h4 style="top:84px">Custom Workshops</h4>
  <p style="top:112px;width:340px">Unique, effective program design and facilitation to match the needs of executives, managers, or promising individuals of any level.</p>
  <div class="more" style="top:192px">More</div>
</div>
<div class="abs tile" style="left:488px;top:1765px;width:712px;height:257px">
  <div class="fill" role="img" aria-label="Notebook and pen on a desk" style="background:
    radial-gradient(ellipse 220px 90px at 340px 60px,rgba(200,210,212,.7) 0,rgba(200,210,212,0) 100%),
    radial-gradient(ellipse 260px 70px at 560px 220px,rgba(60,80,90,.5) 0,rgba(60,80,90,0) 100%),
    linear-gradient(90deg,#506e7a 0%,#8ea2a9 40%,#a6b6bb 60%,#5e7681 100%)"></div>
  <h4 style="left:74px;top:128px">Keynote Speeches</h4>
  <p style="left:74px;top:156px;width:560px">Fresh ways of thinking about speaking and communication combined with practical tools for participants of your next conference or event.</p>
</div>

<!-- publications -->
<h2 class="abs section-title" style="top:2062px">Recent Publications</h2>
<div class="abs cover" style="left:262px;top:2137px;background:
  radial-gradient(ellipse 90px 70px at 105px 150px,rgba(240,200,60,.55) 0,rgba(240,200,60,0) 100%),
  linear-gradient(180deg,#2f9fd8,#3aa4d4 50%,#2c7fb3)" role="img" aria-label="Gentry Quarterly magazine cover"></div>
<div class="abs cover" style="left:495px;top:2137px;background:
  radial-gradient(ellipse 60px 70px at 105px 90px,rgba(230,200,140,.7) 0,rgba(230,200,140,0) 100%),
  radial-gradient(ellipse 90px 80px at 110px 200px,rgba(120,170,210,.7) 0,rgba(120,170,210,0) 100%),
  linear-gradient(180deg,#ece7e1,#c9d6de 60%,#7fa9c9)" role="img" aria-label="Maison Belle magazine cover"></div>
<div class="abs cover" style="left:728px;top:2137px;background:
  radial-gradient(ellipse 55px 70px at 105px 80px,rgba(215,175,140,.8) 0,rgba(215,175,140,0) 100%),
  radial-gradient(ellipse 110px 90px at 105px 220px,rgba(25,25,30,.85) 0,rgba(25,25,30,0) 100%),
  linear-gradient(180deg,#9a2b22,#7a2a22 55%,#3a2a28)" role="img" aria-label="Harbor City Daily feature image"></div>
<div class="abs caption" style="left:262px;top:2424px">Spring/Summer Gentry<br>Quarterly Black Book</div>
<div class="abs caption" style="left:495px;top:2424px">Maison Belle<br>Magazine</div>
<div class="abs caption" style="left:728px;top:2424px">Harbor City<br>Daily</div>

<!-- training -->
<div class="abs training"></div>
<h2 class="abs section-title" style="top:2568px;font-size:27px">BVT Provides Training, Tools, and Techniques</h2>
<p class="abs sub" style="top:2612px">Watch A <em>Free Video</em> With 5 Great Speaking Tips</p>
<ul class="abs checklist">
  <li><svg width="14" height="14" viewBox="0 0 14 14"><circle cx="7" cy="7" r="6" fill="none" stroke="#e8ac2c"/><path d="M4 7l2 2 4-4" fill="none" stroke="#e8ac2c" stroke-width="1.4"/></svg>Executive Presence – Polishing Personal Presentation/Manner</li>
  <li><svg width="14" height="14" viewBox="0 0 14 14"><circle cx="7" cy="7" r="6" fill="none" stroke="#e8ac2c"/><path d="M4 7l2 2 4-4" fill="none" stroke="#e8ac2c" stroke-width="1.4"/></svg>Addressing and Overcoming Speaking/Communication Anxiety</li>
  <li><svg width="14" height="14" viewBox="0 0 14 14"><circle cx="7" cy="7" r="6" fill="none" stroke="#e8ac2c"/><path d="M4 7l2 2 4-4" fill="none" stroke="#e8ac2c" stroke-width="1.4"/></svg>Last-Minute Presentation 911</li>
  <li><svg width="14" height="14" viewBox="0 0 14 14"><circle cx="7" cy="7" r="6" fill="none" stroke="#e8ac2c"/><path d="M4 7l2 2 4-4" fill="none" stroke="#e8ac2c" stroke-width="1.4"/></svg>Media Training</li>
  <li><svg width="14" height="14" viewBox="0 0 14 14"><circle cx="7" cy="7" r="6" fill="none" stroke="#e8ac2c"/><path d="M4 7l2 2 4-4" fill="none" stroke="#e8ac2c" stroke-width="1.4"/></svg>Modifying Accents for Clarity and Intelligibility</li>
  <li><svg width="14" height="14" viewBox="0 0 14 14"><circle cx="7" cy="7" r="6" fill="none" stroke="#e8ac2c"/><path d="M4 7l2 2 4-4" fill="none" stroke="#e8ac2c" stroke-width="1.4"/></svg>Communicating Complex/Technical Material to Any Audience</li>
  <li><svg width="14" height="14" viewBox="0 0 14 14"><circle cx="7" cy="7" r="6" fill="none" stroke="#e8ac2c"/><path d="M4 7l2 2 4-4" fill="none" stroke="#e8ac2c" stroke-width="1.4"/></svg>Cultivating a More Effective Communication Style</li>
  <li><svg width="14" height="14" viewBox="0 0 14 14"><circle cx="7" cy="7" r="6" fill="none" stroke="#e8ac2c"/><path d="M4 7l2 2 4-4" fill="none" stroke="#e8ac2c" stroke-width="1.4"/></svg>Incorporating and Interacting with Audio/Visual Aids</li>
  <li><svg width="14" height="14" viewBox="0 0 14 14"><circle cx="7" cy="7" r="6" fill="none" stroke="#e8ac2c"/><path d="M4 7l2 2 4-4" fill="none" stroke="#e8ac2c" stroke-width="1.4"/></svg>Developing Tools for Dynamic Speaking</li>
  <li><svg width="14" height="14" viewBox="0 0 14 14"><circle cx="7" cy="7" r="6" fill="none" stroke="#e8ac2c"/><path d="M4 7l2 2 4-4" fill="none" stroke="#e8ac2c" stroke-width="1.4"/></svg>Conducting Communication 360° Interviews</li>
  <li><svg width="14" height="14" viewBox="0 0 14 14"><circle cx="7" cy="7" r="6" fill="none" stroke="#e8ac2c"/><path d="M4 7l2 2 4-4" fill="none" stroke="#e8ac2c" stroke-width="1.4"/></svg>Sharpening Presentation Skills for Attorneys</li>
</ul>
<div class="abs video" role="img" aria-label="Video still of the coach presenting speaking tips"></div>
<svg class="abs play" width="50" height="50" viewBox="0 0 50 50"><circle cx="25" cy="25" r="22" fill="none" stroke="#fff" stroke-width="3"/><path d="M20 15l15 10-15 10z" fill="#fff"/></svg>

<!-- signup -->
<div class="abs signup"></div>
<p class="abs signup-text">Register and receive FREE "7 Crimes Against Communication"</p>
<div class="abs field"><span>name@email.com</span></div>
<div class="abs register">Register Now!</div>

<!-- footer -->
<footer class="abs footer"></footer>
<div class="abs f-name">Marian Brightwell</div>
<div class="abs f-role">Public Speaking Consultant</div>
<p class="abs f-text">Providing highly specialized executive coaching services and program design and facilitation for leadership development, public speaking, and all areas of spoken communication.</p>
<div class="abs consult">Consult Now!</div>
<div class="abs f-call">Call Today. 555.014.2290</div>
<div class="abs f-mail">e. info@brightwellvoicetutor.com</div>
<div class="abs social"><span></span><span class="on"></span><span></span><span></span><span></span></div>
<div class="abs f-links">Privacy Policy &nbsp;&nbsp;|&nbsp;&nbsp; Sitemap</div>
<svg class="abs totop" width="22" height="22" viewBox="0 0 26 24"><path d="M3 22L13 2l10 20M8 13h10" fill="none" stroke="#fff" stroke-width="2"/></svg>
<div class="abs copyright">© 2019 Brightwell Voice Tutoring.</div>

</body>
</html>
```